Need a clean & modern homepage for an education site + opportunity for longer term work

Thanks for viewing our project. We are excited about this new website and we hope that we might build a relationship with designers as we work on this project. I provided quite a few details and requirements to help you more quickly create a design that meets our needs.
Who we are:
We are a website that discusses the importance of college accreditation and provides a directory of college programs.
What we need:
A homepage that meets the below requirements and is inspired by the examples provided
Definition of accredited:
ac·cred·it·ed [uh-kred-i-tid] adj.
1. officially recognized as meeting the essential requirements, as of academic excellence: accredited schools.
2. provided with official credentials, as by a government: an accredited diplomatic representative.
3. accepted as authoritative: an accredited theory.
Overall look and feel for the homepage:
- Clean, simple and modern
- Limited (or zero) pictures
- Utilize color blocks with text
- A trend seems to be longer vertical length homepages with lots of whitespace. I generally like this trend as long as the page is not way to tall.
Inspirations: Sites that have a similar look and feel to what I need.
http://lernvoxa.org/
http://www.campusmetrik.com/colleges/brantmoor-university/
http://quietfolding.org/
http://www.velostrahiring.com/
http://www.zunq.com/
http://sketches.bxv.com/
Items to be included on the homepage. Details below on each item.
- Top navigation
- Logo: Please leave a blank area for a logo. The logo has not been designed.
- Simple graphic/color block at the top that highlights a definition of “Accredited” – the definition should be formatted like it is being copy/pasted from a dictionary.
- Space for a video and small (50 word) written description of the video. You can use placeholder text.
- One section with 3 Paragraphs of content (each paragraph around 100 words) with a header at the top. You can use placeholder text but please create the formatting. At the end of the 3 paragraphs please have a “Read More” Note this shouldn't be 3 separate paragraphs with three read mores - it is 3 paragraphs with one read more at the end.
- An area with the header “Search Colleges by State” that has anchor text links to all 50 states.
Top navigation:
- Home
- States – with a subnav dropdown that includes all 50 US states.
- Programs – with a subnav dropdown that includes program titles (list below)
- Degrees - with a subnav dropdown that includes 5 degree levels (list below)
- Accreditation – no subnav
- Rankings – no subnav
- Resources – no subnav
Footer
- Link to about us, privacy, and a copyright www.url.com
Programs List for sub navigation
Accounting
Art
Bible
Business
Criminal Justice
Design
Education
Engineering
English
Law
LPN to RN
Management
Math
MBA
MPH
Medical Assisting
Military
Nursing
Occupational Therapy
Paralegal
Psychology
Pharmacy
RN to BSN
Radiology
Social Work
Sonography
Degrees list for sub navigation
Certificate
Associate
Bachelors
Masters
PhD
Thanks so much - looking forward to working with you!
Education

```html
<!DOCTYPE html>
<html lang="en">
<head>
<meta charset="utf-8">
<title>Accredited Colleges – Home</title>
<link href="https://fonts.googleapis.com/css2?family=Ubuntu:ital,wght@0,300;0,400;0,500;0,700;1,400&family=Tinos:ital,wght@0,400;0,700;1,400;1,700&display=swap" rel="stylesheet">
<style>
:root{
  --ink:#111;
  --text:#4a4a4a;
  --nav-bg:#454545;
  --nav-text:#c4c4c4;
  --accent-red:#f05a48;
  --accent-orange:#f0622e;
  --hero-bg:#ebe9e1;
  --definition-blue:#0aa6e8;
  --card-teal:#22b0cc;
  --card-violet:#8a8cbd;
  --video-green:#16ae7e;
  --title-teal:#3a97ab;
  --footer-bg:#363b47;
  --white:#fff;
}
*{margin:0;padding:0;box-sizing:border-box}
html,body{width:1200px;height:2500px;overflow:hidden}
body{font-family:'Ubuntu',sans-serif;color:var(--text);background:var(--white)}
a{color:inherit;text-decoration:none}

.site-header{height:104px;display:flex;align-items:center;justify-content:center}
.brand{font-weight:700;font-size:50px;color:var(--ink);letter-spacing:1px}

.main-nav{height:56px;background:var(--nav-bg);display:flex;justify-content:center}
.main-nav a{display:flex;align-items:center;gap:8px;padding:0 24px;font-size:14px;font-weight:700;text-transform:uppercase;color:var(--nav-text);letter-spacing:.5px}
.main-nav a.active{background:var(--accent-red);color:var(--white)}
.caret{width:0;height:0;border-left:5px solid transparent;border-right:5px solid transparent;border-top:5px solid currentColor}

.hero{height:398px;background:var(--hero-bg);position:relative}
.definition{position:absolute;left:310px;top:57px;width:578px;height:285px;background:var(--definition-blue);color:var(--white);font-family:'Tinos',serif;padding:36px 56px}
.definition .word{font-size:40px;font-weight:700;letter-spacing:1px}
.definition .pron{font-size:26px;margin-left:12px}
.definition .pos{display:block;font-size:24px;font-style:italic;font-weight:700;margin-top:-2px}
.definition ol{margin-top:24px;padding-left:0;list-style:none;font-size:16.5px;line-height:21px}

.features{display:flex;justify-content:center;gap:21px;padding-top:46px;height:381px}
.feature-card{width:285px;height:302px;color:var(--white);text-align:center;padding-top:28px}
.feature-card.ranking{background:var(--accent-orange)}
.feature-card.accreditation{background:var(--card-teal)}
.feature-card.resources{background:var(--card-violet)}
.feature-card svg{width:62px;height:62px}
.feature-card h2{font-weight:400;font-size:36px;margin:6px 0 10px}
.feature-card p{font-size:13px;font-weight:700;line-height:19px;padding:0 26px}

.video-section{height:473px;background:var(--video-green);color:var(--white);text-align:center;position:relative;padding-top:22px}
.video-section h2{font-weight:300;font-size:46px;letter-spacing:1px}
.video-player{position:absolute;left:367px;top:96px;width:435px;height:236px;background:var(--white)}
.video-frame{height:183px;background:linear-gradient(135deg,#6b5a48,#3a3432 55%,#8a7c6a)}
.video-controls{height:53px;display:flex;align-items:center;gap:16px;padding:0 14px}
.progress{flex:1;height:12px;background:#d7dee6;position:relative}
.progress span{position:absolute;left:0;top:0;height:100%;width:47%;background:#f28080}
.play-overlay{position:absolute;left:182px;top:58px}
.video-pointer{position:absolute;left:812px;top:140px;width:150px;height:130px;border-radius:8px;background:rgba(0,0,0,.07)}
.video-section p{position:absolute;left:152px;top:346px;width:896px;font-size:17px;line-height:22px}

.article{height:477px;padding:40px 150px 0}
.article h2{font-weight:300;font-size:38px;color:var(--title-teal);margin-bottom:24px}
.article p{font-size:15.5px;line-height:34px;color:#555;margin-bottom:16px;hyphens:auto}
.article .clip{height:290px;overflow:hidden}
.btn-readmore{display:inline-block;margin-top:12px;background:var(--accent-orange);color:var(--white);font-size:14px;font-weight:500;text-transform:uppercase;width:121px;height:39px;line-height:39px;text-align:center}

.states{height:358px;background:var(--accent-red);color:var(--white);padding:24px 150px 0}
.states h2{display:flex;align-items:center;gap:22px;font-weight:300;font-size:34px;white-space:nowrap}
.states h2::before,.states h2::after{content:"";flex:1;height:1px;background:rgba(255,255,255,.55)}
.state-grid{display:grid;grid-template-columns:repeat(6,154px);grid-template-rows:repeat(9,27px);grid-auto-flow:column;margin:18px 0 0 19px}
.state-grid a{font-size:16px;font-style:italic;text-decoration:underline;line-height:27px}

.site-footer{height:252px;background:var(--footer-bg);color:var(--white);text-align:center;padding-top:28px}
.site-footer .brand{color:var(--white);font-size:40px}
.social{display:flex;justify-content:center;gap:5px;margin:20px 0 22px}
.social span{width:33px;height:33px;background:#5d6578}
.footer-links{font-size:16px}
.footer-links i{font-style:normal;margin:0 10px}
.footer-url{font-style:italic;font-size:16px;margin-top:14px}
</style>
</head>
<body>
<header class="site-header"><span class="brand">LOGO</span></header>

<nav class="main-nav">
  <a href="#">Home</a>
  <a href="#">States <span class="caret"></span></a>
  <a href="#" class="active">Programs <span class="caret"></span></a>
  <a href="#">Degrees <span class="caret"></span></a>
  <a href="#">Accreditation</a>
  <a href="#">Rankings</a>
  <a href="#">Resources</a>
</nav>

<section class="hero" role="img" aria-label="Tiled pattern of faint education icons">
  <div class="definition">
    <span class="word">ac·cred·it·ed</span><span class="pron">[uh-kred-i-tid]</span>
    <span class="pos">adj</span>
    <ol>
      <li>1. officially recognized as meeting the essential requirements, as of academic excellence: accredited schools.</li>
      <li>2. provided with official credentials, as by a government: an accredited diplomatic representative.</li>
      <li>3. accepted as authoritative: an accredited theory.</li>
    </ol>
  </div>
</section>

<section class="features">
  <article class="feature-card ranking">
    <svg viewBox="0 0 62 62"><circle cx="31" cy="31" r="30" fill="#fff"/><path d="M22 19h18v8a9 9 0 0 1-18 0z M29 36h4v6h5v3H24v-3h5z" fill="var(--accent-orange)"/></svg>
    <h2>Ranking</h2>
    <p>Lorem ipsum dolor sit amet, consectetur adipiscing elit. Fusce rutrum magna in nisi mattis, ut mollis lorem dictum. Morbi ac condimentum lacus. Phasellus dolor magna, rhoncus et interdum eget, tempor non sapien.</p>
  </article>
  <article class="feature-card accreditation">
    <svg viewBox="0 0 62 62"><circle cx="31" cy="31" r="30" fill="#fff"/><circle cx="31" cy="28" r="10" fill="var(--card-teal)"/><path d="M25 36l-3 10 5-2 3 4 1-10z M37 36l3 10-5-2-3 4-1-10z" fill="var(--card-teal)"/></svg>
    <h2>Accreditation</h2>
    <p>Lorem ipsum dolor sit amet, consectetur adipiscing elit. Fusce rutrum magna in nisi mattis, ut mollis lorem dictum. Morbi ac condimentum lacus. Phasellus dolor magna, rhoncus et interdum eget, tempor non sapien.</p>
  </article>
  <article class="feature-card resources">
    <svg viewBox="0 0 62 62"><circle cx="31" cy="31" r="30" fill="#fff"/><path d="M14 28l17-8 17 8-17 8z M21 32v7c5 4 15 4 20 0v-7l-10 5z" fill="var(--card-violet)"/></svg>
    <h2>Resources</h2>
    <p>Lorem ipsum dolor sit amet, consectetur adipiscing elit. Fusce rutrum magna in nisi mattis, ut mollis lorem dictum. Morbi ac condimentum lacus. Phasellus dolor magna, rhoncus et interdum eget, tempor non sapien.</p>
  </article>
</section>

<section class="video-section">
  <h2>WATCH OUR VIDEO</h2>
  <div class="video-player">
    <div class="video-frame" role="img" aria-label="Video still of a presenter speaking in an office"></div>
    <div class="video-controls">
      <svg width="26" height="26" viewBox="0 0 26 26"><circle cx="13" cy="13" r="12" fill="#6d7a8a"/><path d="M10 8l8 5-8 5z" fill="#fff"/></svg>
      <div class="progress"><span></span></div>
      <svg width="24" height="24" viewBox="0 0 24 24" fill="none" stroke="#b8c2cc" stroke-width="2.5"><path d="M3 9V3h6M21 9V3h-6M3 15v6h6M21 15v6h-6M3 3l6 6M21 3l-6 6M3 21l6-6M21 21l-6-6"/></svg>
    </div>
    <svg class="play-overlay" width="70" height="70" viewBox="0 0 70 70"><circle cx="35" cy="35" r="31" fill="rgba(255,255,255,.25)" stroke="#fff" stroke-width="4"/><path d="M28 22l20 13-20 13z" fill="#fff"/></svg>
  </div>
  <div class="video-pointer" role="img" aria-label="Hand-drawn curved arrow pointing down to the video description"></div>
  <p>Lorem ipsum dolor sit amet, consectetur adipiscing elit. Fusce rutrum magna in nisi mattis, ut mollis lorem dictum. Morbi ac condimentum lacus. Phasellus dolor magna, rhoncus et interdum eget, tempor non sapien. Nullam fermentum ultrices ipsum non molestie. Nunc vitae nulla ut felis ultrices mollis nec vel felis. Sed vehicula orci a orci vehicula mattis.</p>
</section>

<section class="article">
  <h2>HEADER TITLE 1</h2>
  <div class="clip">
    <p>Lorem ipsum dolor sit amet, consectetur adipiscing elit. Donec accumsan nec ipsum a auctor. Nulla facilisi. Aliquam erat volutpat. Mauris suscipit diam a eros faucibus, non imperdiet urna porttitor. Nulla at faucibus libero. Donec congue tincidunt volutpat.</p>
    <p>Nulla facilisi. Nulla sit amet vehicula ante. Nunc non sapien neque. In suscipit hendrerit metus id pellentesque.<br>Proin volutpat turpis et rutrum congue. Curabitur eget ipsum volutpat, mollis est in, rutrum velit. Vivamus tellus elit, lacinia ac ullamcorper in, commodo nec nibh.</p>
    <p>Pellentesque sit amet urna nec sem pulvinar pellentesque a a lorem.<br>Proin id ultrices urna. Fusce sed nisi sed augue vehicula semper a consequat nunc. Maecenas eu feugiat erat. Integer tincidunt volutpat.</p>
  </div>
  <a href="#" class="btn-readmore">Readmore</a>
</section>

<section class="states">
  <h2>Search Colleges by State</h2>
  <div class="state-grid">
    <a href="#">Alabama</a><a href="#">Alaska</a><a href="#">Arizona</a><a href="#">Arkansas</a><a href="#">California</a><a href="#">Colorado</a><a href="#">Connecticut</a><a href="#">Delaware</a><a href="#">Florida</a>
    <a href="#">Georgia</a><a href="#">Hawaii</a><a href="#">Idaho</a><a href="#">Illinois</a><a href="#">Indiana</a><a href="#">Iowa</a><a href="#">Kansas</a><a href="#">Kentucky</a><a href="#">Louisiana</a>
    <a href="#">Maine</a><a href="#">Maryland</a><a href="#">Massachusetts</a><a href="#">Michigan</a><a href="#">Minnesota</a><a href="#">Mississippi</a><a href="#">Missouri</a><a href="#">Montana</a><a href="#">Nebraska</a>
    <a href="#">Nevada</a><a href="#">New Hampshire</a><a href="#">New Jersey</a><a href="#">New Mexico</a><a href="#">New York</a><a href="#">North Carolina</a><a href="#">North Dakota</a><a href="#">Ohio</a><a href="#">Oklahoma</a>
    <a href="#">Oregon</a><a href="#">Pennsylvania</a><a href="#">Rhode Island</a><a href="#">South Carolina</a><a href="#">South Dakota</a><a href="#">Tennessee</a><a href="#">Texas</a><a href="#">Utah</a><a href="#">Vermont</a>
    <a href="#">Virginia</a><a href="#">Washington</a><a href="#">West Virginia</a><a href="#">Wisconsin</a><a href="#">Wyoming</a>
  </div>
</section>

<footer class="site-footer">
  <span class="brand">LOGO</span>
  <div class="social" aria-label="Social links"><span></span><span></span><span></span><span></span></div>
  <div class="footer-links"><a href="#">about us</a><i>|</i><a href="#">privacy</a><i>|</i><a href="#">copyright</a></div>
  <div class="footer-url">www.url.com</div>
</footer>
</body>
</html>
```